Remote Game Console (Tavlin) Wpf/Web UI

A complete interface for a second generation remote console tool to administer PC games. Will primarily run as a desktop application with future plans of running within a browser.

All materials are supplied as a guide only, but the designer is free to build what they would find easy to use. We're engineers so help us out with a good user experience.

The first version of Tavlin Emberhold was released in March 2009 supporting Skyrend: Iron Platoon 2. It was updated later in the year to support the expansion, SRIP2: Kestrel. Crest of Valour followed in late 2010 and Skyrend 3 support in October 2011. All games are based on MORV's Emberhold engine. http://dravek.example/tavlin-emberhold/

Tavlin 2 will eventually support all games, working more along the lines of a framework for others to expand upon. While ultimately having a similar function as Tavlin Emberhold, Tavlin 2 has been completely rewritten and shares no similarities internally.

The primary focus of the application is to display details about a users rented Game Server. A user can kick, ban and chat with players in their servers. A user can alter the settings of their game server, setting the time of a round or the game servers name for instance.

We have a forum dedicated to this competition that users of our software can give general feedback about the existing (Tavlin Emberhold) software, such as what they hate etc. http://www.dravek.example/forumvb/forumdisplay.php?35-UI-Competition

You can find similar software with much cooler looking UI's at http://www.ip2xz.example/ and http://sk3xz.example/

The techy details:

Tavlin 2 can run locally or connect and login to a hosted version of the software (internally we call this a Local Interface or Remote Interface). Logging into a remote server requires an IP, port, username and password. Beyond the initial local/remote selection the UI can function identically.

1 Instance of the software has a single Local (no login required) or Remote (ip/port/username/password required) Interface.

1 Instance has many Packages. A package is an extension to the software that the user can install. A package can be an update to Tavlin 2 itself, a plugin or a config.

1 Instance has many Options. We are partial to Nuvex Lumas Options panel. Something similar which would allow us to expand would be neat.

1 Instance has many languages.

1 Interface has many Game Connections. A game connection requires an ip, port and password to connect and authenticate. A game connection has a name, maximum players allowed to connect, a game type (e.g iron platoon 2, crest of valour, skyrend 3).

1 Game Connection has many plugins. A plugin extends the functionality of the software in the background.

1 Game Connection has many players. A player has a name, country, score, ping, kills, deaths and other variables depending on the type of Game connected to.

1 Game Connection has many bans. A ban is a record of a player, the players identifying information, a small description of why the ban was put in place as well as an expiry time (e.g. banned for 2 weeks or permanently banned)

1 Game Connection has many settings. These settings can vary dramatically depending on the Game connected to.

1 Interface has many Groups. A group has a name any many permissions.

1 Group has many Accounts.

1 Account has many players.
Updates

Reason: Uploaded wireframes. I work a lot and this is my side project. I thought I would have wireframes the next day of this project, but it didn't end up like that. All current submissions have been the first iteration of my software reskinned, not the next version.

Target Market(s)

First Person Shooter PC game administrators

Industry/Entity Type

Software

Requirements
Must have
• Tavlin 2 has a primitive natural language parser for converting free text into commands for the program. An online functional example is available at http://labs.venta.example/the-thrifty-helper/ (check down the bottom). The design should incorporate a text box throughout the application for users to enter commands in. As the user types this could be passed to display what will happen once the user executes the command

Generally people will be minimizing their games to kick or ban people from their servers. The UI design should be easy enough to navigate quickly.

A UI that can handle multiple languages. Our primary market is Germany.

The UI must be usable at 1024x768. It should be designed to take up the maximum window/browser space.
Nice to have
• Responsive design that scales to any resolution. We have a large mobile user base that could benefit from a UI that scales well on lower resolutions.

Tavlin 2 has no set logo as of yet, though we will continue using the smiley found at http://dravek.example - we only have a 100 by 100px png of this image though. If a larger version is supplied you'll receive a virtual cookie and a thank you! The logo will probably end up as a variation of that found on http://dravek.example/tavlin-emberhold/ but we'll go through the exact process for this at a later date

```html
<!DOCTYPE html>
<html lang="en">
<head>
<meta charset="utf-8">
<title>Tavlin Emberhold – Events</title>
<link href="https://fonts.googleapis.com/css2?family=PT+Sans:wght@400;700&display=swap" rel="stylesheet">
<style>
:root{
  --bg:#0b0d10;
  --panel:#000000;
  --panel-edge:#3b7fb4;
  --side:#23272c;
  --field:#2c3035;
  --field-edge:#4a4f55;
  --text:#e9eaec;
  --muted:#a3a8ae;
  --info-top:#b9bec4;
  --info-bot:#8d9399;
  --blue-text:#2c5f91;
  --green:#5bc94b;
}
*{box-sizing:border-box;margin:0;padding:0}
html,body{width:996px;height:1200px;overflow:hidden;background:var(--bg)}
body{position:relative;font-family:"PT Sans",Arial,sans-serif;color:var(--text);font-size:12px}
.abs{position:absolute}
.backdrop{left:0;top:125px;width:996px;height:1075px;background:radial-gradient(ellipse at 5% 45%,#3a2a26 0%,#14161a 40%,#0b0d10 75%),radial-gradient(ellipse at 100% 30%,#2a2f35 0%,transparent 40%)}
.titlebar{left:0;top:0;width:996px;height:39px;background:linear-gradient(#4b4e52,#2a2c2f);border-bottom:1px solid #111}
.app-name{left:36px;top:12px;font-size:12px;color:#d7d9dc}
.app-dot{left:14px;top:12px;width:14px;height:14px;border-radius:50%;background:#cfd3d7;border:3px solid #2a2c2f;box-shadow:0 0 0 1px #777}
.winbtns{right:10px;top:3px;display:flex;gap:2px}
.winbtns span{width:27px;height:17px;background:linear-gradient(#6a6d71,#3b3d40);border:1px solid #222;display:flex;align-items:center;justify-content:center}
.winbtns span.close{width:44px;background:linear-gradient(#d9573f,#a02a16)}
.menubar{left:0;top:39px;width:996px;height:41px;background:linear-gradient(#34373b,#2b2e32);display:flex;gap:20px;padding:15px 0 0 37px;font-size:13px;color:#d5d7da}
.toolbar{left:0;top:80px;width:996px;height:45px;background:linear-gradient(#4a4e53,#2e3135);border-top:1px solid #5b5f64;border-bottom:1px solid #15171a}
.server-select{left:196px;top:6px;width:450px;height:29px;background:#0e1013;border:1px solid #6a6f75;border-radius:3px;display:flex;align-items:center;padding-left:8px;gap:7px;font-size:10px;color:#b6bac0;white-space:nowrap;overflow:hidden}
.game-name{font-size:12px;color:#e7e7e7}
.auto-btn{left:682px;top:12px;width:133px;height:21px;background:linear-gradient(#d24a30,#a52b17);border:1px solid #6d1a0d;border-radius:2px;font-size:10px;display:flex;align-items:center;justify-content:center;gap:5px;white-space:nowrap}
.infobar{left:0;top:125px;width:996px;height:42px;background:linear-gradient(var(--info-top),var(--info-bot));color:#121416;font-size:12px}
.infobar span{white-space:nowrap}
.infobar .map{left:37px;top:14px;font-weight:700}
.infobar .round{left:141px;top:14px}
.infobar .status{left:339px;top:14px;color:var(--blue-text)}
.infobar .ver{left:447px;top:14px}
.infobar .ver b{color:var(--blue-text);font-weight:400;margin-left:8px}
.tab{position:absolute;top:182px;height:29px;display:flex;align-items:center;justify-content:center;white-space:nowrap;background:linear-gradient(#484c51,#2b2e32);border:1px solid #5a5e63;border-bottom:none;border-radius:3px 3px 0 0;font-size:12px}
.tab.active{background:linear-gradient(#c9482f,#9c2c19);border-color:#d45a42}
.main{left:31px;top:212px;width:934px;height:817px;background:var(--panel);border:1px solid var(--panel-edge)}
.thead{left:6px;top:18px;width:661px;height:34px;background:linear-gradient(#3c4045,#25282c);font-size:12px}
.thead span{position:absolute;top:9px}
.rows{left:8px;top:64px;width:650px;border-collapse:collapse;font-size:11.5px;letter-spacing:-.2px}
.rows td{height:19.46px;white-space:nowrap;padding:0;vertical-align:middle}
.c1{width:61px}.c2{width:68px}.c3{width:59px}.c4{width:124px}
.scroll{left:661px;top:84px;width:10px;height:724px;background:#1a1c1f;border:1px solid #333;border-radius:4px}
.scroll i{position:absolute;left:1px;top:160px;width:6px;height:180px;background:#3a3e43;border-radius:3px}
.captures{left:686px;top:18px;width:238px;height:774px;background:var(--side);border-radius:3px}
.cap-title{left:8px;top:16px;font-size:13px}
.cap-close{right:8px;top:16px;font-size:10px;color:var(--muted)}
.label{font-size:12px;color:#e2e4e7}
.field{background:var(--field);border:1px solid var(--field-edge);border-radius:3px;font-size:11px;color:var(--muted);display:flex;align-items:center;padding-left:8px}
.evlist{left:14px;top:199px;width:185px;height:537px;background:#2a2e33;border:1px solid #3a3e44}
.evlist ul{list-style:none;padding:5px 0 0 19px;font-size:12px;color:#8e939a;line-height:21.4px}
.evscroll{right:2px;top:4px;width:8px;height:527px;background:#1d2024;border-radius:4px}
.evscroll i{position:absolute;left:1px;top:170px;width:6px;height:180px;background:#4a4e54;border-radius:3px}
.round-icon{width:14px;height:14px;border-radius:50%;background:#8a8f95;color:#2a2e33;font-size:12px;line-height:14px;text-align:center;font-weight:700}
.clear-ev{left:78px;top:757px;width:100px;height:20px;background:linear-gradient(#3c4045,#2a2d31);border:1px solid #4c5056;font-size:11px;display:flex;align-items:center;justify-content:center}
.chat-input{left:49px;top:1063px;width:525px;height:27px;background:#3a3e43;border:1px solid #4f5359;border-radius:3px}
.sel{height:27px;background:linear-gradient(#4e5257,#35383c);border:1px solid #5b5f64;border-radius:2px;display:flex;align-items:center;justify-content:space-between;padding:0 7px;font-size:12px;white-space:nowrap;gap:6px}
.sel::after{content:"";border:4px solid transparent;border-top:5px solid #ddd;margin-top:4px}
.hint{font-size:12px;color:#cfd2d6}
.btn-send{left:847px;top:1063px;width:86px;height:27px;background:linear-gradient(#3c79ad,#24527e);border:1px solid #5b92c2;border-radius:2px;display:flex;align-items:center;justify-content:center;font-size:13px}
.btn-clear{left:847px;top:1105px;width:86px;height:27px;background:linear-gradient(#d24a30,#a52b17);border:1px solid #e06a52;border-radius:2px;display:flex;align-items:center;justify-content:center;font-size:13px}
.check{left:50px;display:flex;align-items:center;gap:9px;font-size:11.5px;color:#cfd2d6}
.check i{width:10px;height:10px;background:#c8ccd0;border:1px solid #888;display:flex;align-items:center;justify-content:center;font-style:normal;font-size:8px;color:#222}
</style>
</head>
<body>
<div class="abs backdrop" role="img" aria-label="Dark atmospheric game artwork behind the interface"></div>

<header class="abs titlebar">
  <div class="abs app-dot"></div>
  <div class="abs app-name">Tavlin Emberhold</div>
  <div class="abs winbtns">
    <span><svg width="12" height="8"><path d="M1 4l3-3v6zM11 4l-3-3v6z" fill="#eee"/></svg></span>
    <span><svg width="10" height="9"><rect x="1" y="1" width="8" height="7" fill="none" stroke="#eee"/></svg></span>
    <span><svg width="10" height="9"><rect x="1" y="6" width="8" height="2" fill="#eee"/></svg></span>
    <span><svg width="10" height="9"><rect x="1" y="1" width="8" height="7" fill="none" stroke="#eee" stroke-width="1.6"/></svg></span>
    <span class="close"><svg width="10" height="9"><path d="M1 1l8 7M9 1l-8 7" stroke="#fff" stroke-width="1.8"/></svg></span>
  </div>
</header>

<nav class="abs menubar"><span>File</span><span>Tools</span><span>Help</span></nav>

<div class="abs toolbar">
  <svg class="abs" style="left:35px;top:12px" width="26" height="22"><path d="M3 11L13 2l10 9M6 9v11h14V9" fill="none" stroke="#9aa0a6" stroke-width="2.4"/></svg>
  <svg class="abs" style="left:86px;top:14px" width="56" height="18"><path d="M22 9H4m6-6L4 9l6 6M34 9h18m-6-6l6 6-6 6" fill="none" stroke="#8d9298" stroke-width="2.2"/></svg>
  <div class="abs server-select">
    <span class="game-name">Skyrend</span>
    <svg width="12" height="10"><path d="M1 5l3.5 3.5L11 1" stroke="var(--green)" stroke-width="2.4" fill="none"/></svg>
    <span>[ 32/32 ] Tavlin [hxlan.example - Deine Community! --&gt; www.hxlan.example] |</span>
    <svg class="abs" style="right:8px;top:11px" width="10" height="6"><path d="M0 0h10L5 6z" fill="#ddd"/></svg>
  </div>
  <svg class="abs" style="left:660px;top:14px" width="14" height="14"><path d="M2 12l4-4M8 2l4 4-5 5-4-4z" stroke="#777" stroke-width="2" fill="none"/></svg>
  <div class="abs auto-btn"><svg width="11" height="9"><path d="M1 4.5l3 3L10 1" stroke="#8fe07f" stroke-width="2" fill="none"/></svg>Automatically Connect</div>
</div>

<div class="abs infobar">
  <span class="abs map">Rush - Corvessa</span>
  <span class="abs round">Round: 1/2</span>
  <svg class="abs" style="left:219px;top:13px" width="20" height="18"><circle cx="10" cy="9" r="7" fill="none" stroke="#7d838a" stroke-width="3"/></svg>
  <svg class="abs" style="left:254px;top:13px" width="20" height="18"><path d="M2 10l8-8 8 8h-5v6H7v-6z" fill="#7d838a"/></svg>
  <span class="abs status">Accepting Players</span>
  <span class="abs ver">Version: 584642 (R23)<b>0.6.2.0</b></span>
</div>

<nav>
  <div class="tab" style="left:34px;width:70px">Players</div>
  <div class="tab" style="left:113px;width:55px">Chats</div>
  <div class="tab" style="left:174px;width:50px">Map</div>
  <div class="tab active" style="left:228px;width:65px">Events</div>
  <div class="tab" style="left:298px;width:56px">Lists</div>
  <div class="tab" style="left:359px;width:101px">Server Settings</div>
  <div class="tab" style="left:465px;width:74px">Plugins</div>
  <div class="tab" style="left:543px;width:80px">Accounts</div>
  <div class="tab" style="left:625px;width:72px">Console</div>
  <div class="tab" style="left:702px;width:131px">Parent Layer Control</div>
</nav>

<main class="abs main">
  <div class="abs thead">
    <span style="left:8px">Source</span><span style="left:72px">Date</span><span style="left:141px">Time</span><span style="left:200px">Event</span><span style="left:327px">Message</span>
  </div>
  <table class="abs rows">
    <tr><td class="c1">Playerlist</td><td class="c2">02.22.2012</td><td class="c3">03:54:32</td><td class="c4">PlayerSwitchedSquads</td><td>Dunrekt swapped from squad Alpha to Charlie</td></tr>
    <tr><td>Playerlist</td><td>02.22.2012</td><td>03:54:32</td><td>PlayerSwitchedSquads</td><td>Cras interdum augue ac ante faucibus consectetur</td></tr>
    <tr><td>Playerlist</td><td>02.22.2012</td><td>03:54:32</td><td>PlayerSwitchedSquads</td><td>Sed semper dignissim massa, vel posuere nulla accumsan ne</td></tr>
    <tr><td>Playerlist</td><td>02.22.2012</td><td>03:54:32</td><td>PlayerSwitchedSquads</td><td>Donec sodales velit nulla, in posuere purus</td></tr>
    <tr><td>Playerlist</td><td>02.22.2012</td><td>03:54:32</td><td>PlayerSwitchedSquads</td><td>Fusce scelerisque mollis felis, vel molestie justo dignissim eu</td></tr>
    <tr><td>Playerlist</td><td>02.22.2012</td><td>03:54:32</td><td>PlayerSwitchedSquads</td><td>Fusce vulputate nisi sed massa elementum sit amet dapibu</td></tr>
    <tr><td>Playerlist</td><td>02.22.2012</td><td>03:54:32</td><td>PlayerSwitchedSquads</td><td>Nunc ultrices congue tellus, id scelerisque neque facilisis ac</td></tr>
    <tr><td>Playerlist</td><td>02.22.2012</td><td>03:54:32</td><td>PlayerKilled</td><td>Proin vitae lorem eu arcu aliquet consectetur</td></tr>
    <tr><td>Playerlist</td><td>02.22.2012</td><td>03:54:32</td><td>PlayerSwitchedSquads</td><td>Dunrekt swapped from squad Alpha to Charlie</td></tr>
    <tr><td>Playerlist</td><td>02.22.2012</td><td>03:54:32</td><td>PlayerKilled</td><td>Nulla rhoncus urna et nibh volutpat quis mattis nisi ullamcorpe</td></tr>
    <tr><td>Playerlist</td><td>02.22.2012</td><td>03:54:32</td><td>PlayerSwitchedSquads</td><td>Mauris elementum mi at mi placerat eget pharetra justo plac</td></tr>
    <tr><td>Playerlist</td><td>02.22.2012</td><td>03:54:32</td><td>PlayerSwitchedSquads</td><td>Fusce sit amet lectus sed felis volutpat convallis at eu mi.</td></tr>
    <tr><td>Playerlist</td><td>02.22.2012</td><td>03:54:32</td><td>PlayerSwitchedSquads</td><td>Phasellus ut sapien vitae turpis gravida facilisis</td></tr>
    <tr><td>Playerlist</td><td>02.22.2012</td><td>03:54:32</td><td>PlayerSwitchedSquads</td><td>Suspendisse at ligula et arcu consequat rhoncus at eu nunc</td></tr>
    <tr><td>Playerlist</td><td>02.22.2012</td><td>03:54:32</td><td>PlayerSwitchedSquads</td><td>Integer nec neque orci, in rutrum ligula</td></tr>
    <tr><td>Playerlist</td><td>02.22.2012</td><td>03:54:32</td><td>PlayerKilled</td><td>Cras non risus eget arcu lobortis pellentesqu</td></tr>
    <tr><td>Playerlist</td><td>02.22.2012</td><td>03:54:32</td><td>PlayerKilled</td><td>In eget dolor vel enim mattis auctor</td></tr>
    <tr><td>Playerlist</td><td>02.22.2012</td><td>03:54:32</td><td>PlayerKilled</td><td>Donec posuere porttitor dolor, et pharetra enim sodales</td></tr>
    <tr><td>Playerlist</td><td>02.22.2012</td><td>03:54:32</td><td>PlayerKilled</td><td>Maecenas ac orci nisl, id imperdiet sem</td></tr>
    <tr><td>Playerlist</td><td>02.22.2012</td><td>03:54:32</td><td>PlayerSwitchedSquads</td><td>Cras vel turpis nibh, ut aliquet diam</td></tr>
    <tr><td>Playerlist</td><td>02.22.2012</td><td>03:54:32</td><td>PlayerSwitchedSquads</td><td>Donec aliquet lacus eget erat condimentum faucibus</td></tr>
    <tr><td>Playerlist</td><td>02.22.2012</td><td>03:54:32</td><td>PlayerKilled</td><td>Nulla id orci quis dui ornare sagittis a in massa</td></tr>
    <tr><td>Playerlist</td><td>02.22.2012</td><td>03:54:32</td><td>PlayerKilled</td><td>Etiam et dolor vel ipsum mollis ultrices et eget</td></tr>
    <tr><td>Playerlist</td><td>02.22.2012</td><td>03:54:32</td><td>PlayerKilled</td><td>Fusce scelerisque mollis felis, vel molestie justo dignissim eu</td></tr>
    <tr><td>Playerlist</td><td>02.22.2012</td><td>03:54:32</td><td>PlayerKilled</td><td>Dunrekt swapped from squad Alpha to Charlie</td></tr>
    <tr><td>Playerlist</td><td>02.22.2012</td><td>03:54:32</td><td>PlayerKilled</td><td>Fusce vulputate nisi sed massa elementum sit amet dapibus</td></tr>
    <tr><td>Playerlist</td><td>02.22.2012</td><td>03:54:32</td><td>PlayerKilled</td><td>Dunrekt swapped from squad Alpha to Charlie</td></tr>
    <tr><td>Playerlist</td><td>02.22.2012</td><td>03:54:32</td><td>PlayerKilled</td><td>Dunrekt swapped from squad Alpha to Charlie</td></tr>
    <tr><td></td><td>02.22.2012</td><td>03:54:32</td><td>LevelLoading</td><td>Levels / MP_002</td></tr>
    <tr><td></td><td>02.22.2012</td><td>03:54:32</td><td>LevelStarted</td><td></td></tr>
    <tr><td>Playerlist</td><td>02.22.2012</td><td>03:54:32</td><td>PlayerSwitchedSquads</td><td>Nostrud exercitation ullamco laboris nisi ut aliquip ex</td></tr>
    <tr><td>Playerlist</td><td>02.22.2012</td><td>03:54:32</td><td>PlayerSwitchedSquads</td><td>Cras vel turpis nibh, ut aliquet diam</td></tr>
    <tr><td>Playerlist</td><td>02.22.2012</td><td>03:54:32</td><td>PlayerSwitchedSquads</td><td>Donec aliquet lacus eget erat condimentum faucibust</td></tr>
    <tr><td>Playerlist</td><td>02.22.2012</td><td>03:54:32</td><td>PlayerSwitchedSquads</td><td>Mauris elementum mi at mi placerat eget pharetra justo plac</td></tr>
    <tr><td>Playerlist</td><td>02.22.2012</td><td>03:54:32</td><td>PlayerSwitchedSquads</td><td>Fusce sit amet lectus sed felis volutpat convallis at eu mi.</td></tr>
    <tr><td>Playerlist</td><td>02.22.2012</td><td>03:54:32</td><td>PlayerSwitchedSquads</td><td>Phasellus ut sapien vitae turpis gravida facilisis</td></tr>
    <tr><td>Playerlist</td><td>02.22.2012</td><td>03:54:32</td><td>PlayerSwitchedSquads</td><td>Suspendisse at ligula et arcu consequat rhoncus at eu nunc</td></tr>
  </table>
  <div class="abs scroll"><i></i></div>

  <aside class="abs captures">
    <div class="abs cap-title">Captures</div>
    <div class="abs cap-close">Close <b style="color:#4d8cc4;font-size:13px">✕</b></div>
    <div class="abs label" style="left:14px;top:52px">Maximum captures</div>
    <div class="abs field" style="left:14px;top:71px;width:140px;height:24px">100000</div>
    <div class="abs label" style="left:14px;top:110px">Events</div>
    <div class="abs field" style="left:14px;top:129px;width:138px;height:24px;background:#33373c;color:#e4e6e8">Player Join
      <svg class="abs" style="right:8px;top:9px" width="9" height="6"><path d="M0 0h9L4.5 6z" fill="#ddd"/></svg></div>
    <div class="abs round-icon" style="left:214px;top:133px">+</div>
    <div class="abs label" style="left:14px;top:172px">Capturing Events</div>
    <div class="abs evlist">
      <ul>
        <li>Player Join</li><li>Player Leave</li><li>Level Started</li><li>Level Ended</li><li>Map Change</li><li>Connected</li><li>DisConnected</li><li>Lost Connection</li><li>Reconnected</li><li>Round Change</li><li>IPUnbanned</li>
        <li>Player Join</li><li>Player Leave</li><li>Level Started</li><li>Level Ended</li><li>Map Change</li><li>Connected</li><li>DisConnected</li><li>Lost Connection</li><li>Reconnected</li><li>Round Change</li><li>IPUnbanned</li><li>Player Join</li><li>Player Leave</li>
      </ul>
      <div class="abs evscroll"><i></i></div>
    </div>
    <div class="abs round-icon" style="left:214px;top:461px;font-size:10px">×</div>
    <div class="abs clear-ev">Clear Eventlist</div>
  </aside>
</main>

<div class="abs hint" style="left:586px;top:1044px">Audience</div>
<div class="abs hint" style="left:674px;top:1044px">Display</div>
<div class="abs hint" style="left:744px;top:1044px">Display Time</div>
<div class="abs chat-input"></div>
<div class="abs sel" style="left:582px;top:1063px;width:86px;font-weight:700">All Players</div>
<div class="abs sel" style="left:672px;top:1063px;width:66px">Say</div>
<div class="abs sel" style="left:745px;top:1063px;width:90px">2 Seconds</div>
<div class="abs btn-send">Send</div>
<div class="abs btn-clear">Clear Chat</div>
<div class="abs check" style="top:1104px"><i>✓</i>Enable Scrolling</div>
<div class="abs check" style="top:1133px"><i>✓</i>Display join / leaving</div>
<div class="abs check" style="top:1162px"><i>✓</i>Display kills / deaths</div>
</body>
</html>
```